Fine Art business needs new website

We need a simple website with a home page, about us page, New sculptures, Sold sculptures, and a contact us page.Our sculptures are very high end one of a kind pieces. As such we need the site to be VERY elegant and professional. Lastly, because I'll be updating pictures on the website on a monthly basis it needs to be user friendly to update (Wordpress is preferred). The only branding we have so far for the business is a business card.
Updates
I wasn't completely ready when this project launched, also I am on the road right now and haven't been able to be as responsive to all you designers as I would like. I will work on giving feedback to all the top designs we've received so far. Thank you all so much for your participation and hardwork.
Target Market(s)
High end customers (affluent), art collectors, interior decorators/designers
Industry/Entity Type
Art Gallery
Coding
Coded - Design and coding required
Number of Pages Required
5+ page
Requirements
Must have
- Easily editable picture gallery for myself so that I can add new pieces(pictures of the pieces), remove sold pieces, etc. I would like the website to be built in wordpress so I can update it. I currently use mangewordpress through Netmarro for my other business website and would like to do the same for this one.
- Pages:
- -Intro page with featured pieces
- -Current pieces gallery (for sale) mainly a picture gallery
- -Sculptures archive (sold pieces) another picture gallery
- -About us: Pull-down of -about the artist (attached content)
- -Artistic Process (attached content)
- -Show Schedule:
- -one page dedicated to "friends of TMV" (basically a link page)
- TO BE CLEAR "www.pineroverslane.com" IS A TOTALLY DIFFERENT SITE AND I'M NOT TRYING TO COMBINE THE TWO OR JOIN THEM INTO ONE. This page needs be more elegant and seperate from the Pine Rovers site.
- UPDATE: I'd like a link to the TMV Facebook page: https://www.faceplume-social.com/mirelcraftworks/
Nice to have
- I would like the pictures on the gallery pages able to have text connected with them (Materials, price)
- I would like the site style and fonts to be similar to our business cards we've already had designed (picture attached).
Should not have
- Too much flash or other things that will make the site slow to load.

```html
<!DOCTYPE html>
<html lang="en">
<head>
<meta charset="utf-8">
<title>The Mineral Vault — Sculptures</title>
<link rel="stylesheet" href="https://fonts.googleapis.com/css2?family=Cinzel:wght@400;500&family=Poppins:wght@400;500;600&display=swap">
<style>
:root{
  --backdrop:#f4e4fb;
  --paper:#ffffff;
  --ink:#1d1d1d;
  --muted:#555555;
  --rule:#dcdcdc;
  --brand:#4c0f8e;
  --brand-deep:#2e1a48;
  --badge:#e3141c;
  --social-purple:#4b1790;
  --social-plum:#8a1f78;
  --social-red:#d3202a;
  --social-blue:#1f5aa8;
  --card-shadow:0 4px 18px rgba(40,20,60,.14);
}
*{box-sizing:border-box;margin:0;padding:0}
html,body{width:1200px;height:4444px;overflow:hidden}
body{background:var(--backdrop);font-family:'Poppins',sans-serif;color:var(--ink);position:relative}

.page{position:absolute;left:83px;width:1034px;background:var(--paper)}
.page--new{top:80px;height:2326px}
.page--sold{top:2477px;height:1887px}

/* header */
.site-header{position:relative;height:160px}
.contact-list{position:absolute;left:88px;top:8px;list-style:none}
.contact-list li{display:flex;align-items:center;gap:12px;font-size:11px;color:var(--muted);height:20px;margin-bottom:12px}
.contact-icon{width:18px;height:18px;border-radius:50%;background:#3a3a3a;display:flex;align-items:center;justify-content:center}
.brand{position:absolute;left:50%;top:30px;transform:translateX(-50%);display:flex;flex-direction:column;align-items:center;gap:14px}
.brand-mark{width:46px;height:46px;background:var(--brand)}
.brand-name{font-family:'Cinzel',serif;font-size:22px;letter-spacing:3px;color:var(--brand-deep);font-weight:400;white-space:nowrap}
.social-list{position:absolute;right:90px;top:5px;display:flex;gap:20px;list-style:none}
.social-dot{width:26px;height:26px;border-radius:50%;display:flex;align-items:center;justify-content:center}
.social-dot--1{background:var(--social-purple)}
.social-dot--2{background:var(--social-plum)}
.social-dot--3{background:var(--social-red)}
.social-dot--4{background:var(--social-blue)}

/* nav */
.main-nav{height:41px;border-top:1px solid var(--rule);display:flex;justify-content:center;align-items:center;gap:62px;font-size:11px;font-weight:500;letter-spacing:.5px}
.main-nav a{color:var(--ink);text-decoration:none}

/* hero */
.hero{height:288px;display:flex;align-items:center;justify-content:center;
  background:radial-gradient(circle at 25% 40%,#7c4fb4 0%,transparent 40%),radial-gradient(circle at 78% 30%,#a57fd2 0%,transparent 35%),linear-gradient(135deg,#2a1240 0%,#51287e 45%,#3b1a5f 70%,#1c0c2c 100%)}
.page--sold .hero{height:285px}
.hero-title{font-family:'Cinzel',serif;font-weight:400;font-size:58px;color:#fff;letter-spacing:1px;text-shadow:0 2px 8px rgba(0,0,0,.35)}

/* gallery */
.section-title{font-family:'Cinzel',serif;font-weight:400;font-size:36px;line-height:44px;text-align:center;letter-spacing:1px;margin-top:79px}
.page--sold .section-title{margin-top:82px}
.gallery{display:grid;grid-template-columns:repeat(3,278px);column-gap:18px;row-gap:46px;justify-content:center;margin-top:34px}
.page--sold .gallery{row-gap:30px;margin-top:37px}
.card{background:var(--paper);box-shadow:var(--card-shadow)}
.card-photo{position:relative;height:246px}
.badge{position:absolute;left:9px;top:10px;background:var(--badge);color:#fff;font-size:8px;font-weight:600;padding:3px 8px;border-radius:8px;letter-spacing:.3px}
.card-body{height:71px;display:flex;align-items:center;justify-content:space-between;padding:0 18px 0 20px}
.card-name{font-size:14px;font-weight:500;line-height:20px}
.card-price{font-size:12px;color:var(--muted);line-height:18px}
.buy-button{width:100px;height:34px;background:var(--brand);color:#fff;font-size:11px;font-weight:500;letter-spacing:.5px;display:flex;align-items:center;justify-content:center}
.card--sold .card-body{height:65px;padding-bottom:12px}
.card--sold .card-price{font-size:12px}

.tone-amber{background:radial-gradient(ellipse at 50% 50%,#b36a2a 0%,#5a2e10 35%,#0c0806 70%)}
.tone-green{background:radial-gradient(ellipse at 50% 50%,#3f8d70 0%,#1d3d33 35%,#080a09 70%)}
.tone-gold{background:radial-gradient(ellipse at 50% 45%,#d08a2a 0%,#6b3d10 30%,#0a0705 68%)}
.tone-horn{background:radial-gradient(ellipse at 50% 55%,#a27a3c 0%,#4c3418 30%,#0b0806 66%)}
.tone-rose{background:radial-gradient(ellipse at 50% 50%,#8a6a60 0%,#3e2c28 32%,#0a0808 68%)}
.tone-violet{background:radial-gradient(ellipse at 50% 50%,#6a3aa8 0%,#2e1a4e 34%,#080609 70%)}
.tone-blue{background:radial-gradient(ellipse at 50% 50%,#4a5fa8 0%,#22284e 34%,#07070b 70%)}
.tone-indigo{background:radial-gradient(ellipse at 50% 50%,#5a3ab0 0%,#281a5a 34%,#08060c 70%)}
.tone-agate{background:radial-gradient(ellipse at 50% 50%,#b9b8b0 0%,#505060 34%,#09090b 70%)}
.tone-linen{background:linear-gradient(180deg,#e8e4dc 0%,#c9c2b4 50%,#6e6a62 100%)}
.tone-ice{background:linear-gradient(135deg,#3a3a40 0%,#9aa6b4 40%,#5a6070 70%,#c86a20 100%)}
.tone-geode{background:radial-gradient(ellipse at 50% 50%,#8a6ea8 0%,#b8a488 40%,#d6c0b4 65%,#e7a0b8 100%)}
.tone-crystal{background:radial-gradient(ellipse at 50% 50%,#8a5ab0 0%,#3a2a58 40%,#0a0a0e 75%)}
.tone-druzy{background:radial-gradient(ellipse at 50% 50%,#3a4a6a 0%,#6a4a3a 40%,#b49a80 70%,#4a3a30 100%)}

.view-all{display:flex;align-items:center;justify-content:center;width:131px;height:38px;margin:95px auto 0;background:var(--brand);color:#fff;font-size:12px;font-weight:500;letter-spacing:.5px}
.page--sold .view-all{margin-top:44px}

/* footer */
.site-footer{text-align:center;margin-top:89px}
.footer-brand{height:83px;display:flex;flex-direction:column;align-items:center;justify-content:center;gap:10px}
.footer-brand .brand-mark{width:34px;height:34px}
.footer-brand .brand-name{font-size:15px;letter-spacing:2px}
.footer-title{font-family:'Cinzel',serif;font-weight:400;font-size:22px;line-height:30px;margin-top:24px;letter-spacing:.5px}
.footer-text{font-size:13px;line-height:24px;color:#333;margin-top:8px}
.subscribe{display:flex;justify-content:center;margin-top:23px}
.subscribe-input{width:284px;height:36px;border:1px solid #bdbdbd;border-right:none;font-size:11px;color:#777;display:flex;align-items:center;padding-left:14px;text-align:left}
.subscribe-button{width:107px;height:36px;background:var(--brand-deep);color:#fff;font-size:11px;font-weight:500;letter-spacing:.5px;display:flex;align-items:center;justify-content:center}
.footer-social{display:flex;justify-content:center;gap:20px;margin-top:28px;list-style:none}
.copyright{font-size:11px;line-height:16px;color:#555;margin-top:74px}
</style>
</head>
<body>

<!-- New sculptures page -->
<section class="page page--new">
  <header class="site-header">
    <ul class="contact-list">
      <li><span class="contact-icon"><svg width="10" height="10" viewBox="0 0 24 24"><path fill="#fff" d="M6.6 10.8a15 15 0 0 0 6.6 6.6l2.2-2.2c.3-.3.7-.4 1-.2 1.1.4 2.3.6 3.6.6.6 0 1 .4 1 1V20c0 .6-.4 1-1 1A17 17 0 0 1 3 4c0-.6.4-1 1-1h3.5c.6 0 1 .4 1 1 0 1.3.2 2.5.6 3.6.1.3 0 .7-.2 1z"/></svg></span>(555) 014-2290</li>
      <li><span class="contact-icon"><svg width="10" height="10" viewBox="0 0 24 24"><path fill="#fff" d="M2 5h20v14H2zm2 2v.5l8 5 8-5V7l-8 5z"/></svg></span>mara@pineroverslane.com</li>
    </ul>
    <div class="brand"><span class="brand-mark"></span><span class="brand-name">THE MINERAL VAULT</span></div>
    <ul class="social-list">
      <li class="social-dot social-dot--1"></li>
      <li class="social-dot social-dot--2"></li>
      <li class="social-dot social-dot--3"></li>
      <li class="social-dot social-dot--4"><svg width="12" height="12" viewBox="0 0 24 24"><path fill="#fff" d="M2 5h20v14H2zm2 2v.5l8 5 8-5V7l-8 5z"/></svg></li>
    </ul>
  </header>
  <nav class="main-nav">
    <a href="#">HOME</a><a href="#">ABOUT US</a><a href="#">NEW SCULPTURES</a><a href="#">SOLD SCULPTURES</a><a href="#">CONTACT US</a>
    <svg width="11" height="11" viewBox="0 0 24 24"><circle cx="10" cy="10" r="7" fill="none" stroke="#1d1d1d" stroke-width="3"/><path d="M15 15l7 7" stroke="#1d1d1d" stroke-width="3"/></svg>
  </nav>
  <div class="hero" role="img" aria-label="Close-up photograph of purple amethyst crystals">
    <h1 class="hero-title">NEW SCULPTURES</h1>
  </div>

  <h2 class="section-title">NEW SCULPTURE</h2>
  <div class="gallery">
    <article class="card"><div class="card-photo tone-amber" role="img" aria-label="Amber stone sculpture on a dark stand"><span class="badge">FOR SALE</span></div><div class="card-body"><div><p class="card-name">SCULPTURE-1</p><p class="card-price">$12.00</p></div><span class="buy-button">BUY NOW</span></div></article>
    <article class="card"><div class="card-photo tone-green" role="img" aria-label="Green malachite sculpture on a stand"><span class="badge">AVAILABLE</span></div><div class="card-body"><div><p class="card-name">SCULPTURE-1</p><p class="card-price">$12.00</p></div><span class="buy-button">BUY NOW</span></div></article>
    <article class="card"><div class="card-photo tone-gold" role="img" aria-label="Golden agate slice sculpture"><span class="badge">AVAILABLE</span></div><div class="card-body"><div><p class="card-name">SCULPTURE-1</p><p class="card-price">$12.00</p></div><span class="buy-button">BUY NOW</span></div></article>
    <article class="card"><div class="card-photo tone-horn" role="img" aria-label="Curved fossil and horn sculpture"><span class="badge">FOR SALE</span></div><div class="card-body"><div><p class="card-name">SCULPTURE-1</p><p class="card-price">$12.00</p></div><span class="buy-button">BUY NOW</span></div></article>
    <article class="card"><div class="card-photo tone-rose" role="img" aria-label="Carved rose stone sculpture on a base"><span class="badge">AVAILABLE</span></div><div class="card-body"><div><p class="card-name">SCULPTURE-1</p><p class="card-price">$12.00</p></div><span class="buy-button">BUY NOW</span></div></article>
    <article class="card"><div class="card-photo tone-violet" role="img" aria-label="Violet crystal slab sculpture"><span class="badge">FOR SALE</span></div><div class="card-body"><div><p class="card-name">SCULPTURE-1</p><p class="card-price">$12.00</p></div><span class="buy-button">BUY NOW</span></div></article>
    <article class="card"><div class="card-photo tone-blue" role="img" aria-label="Blue twisted stone sculpture"><span class="badge">AVAILABLE</span></div><div class="card-body"><div><p class="card-name">SCULPTURE-1</p><p class="card-price">$12.00</p></div><span class="buy-button">BUY NOW</span></div></article>
    <article class="card"><div class="card-photo tone-indigo" role="img" aria-label="Amethyst cluster sculpture"><span class="badge">FOR SALE</span></div><div class="card-body"><div><p class="card-name">SCULPTURE-1</p><p class="card-price">$12.00</p></div><span class="buy-button">BUY NOW</span></div></article>
    <article class="card"><div class="card-photo tone-agate" role="img" aria-label="Grey agate sculpture on a stand"><span class="badge">AVAILABLE</span></div><div class="card-body"><div><p class="card-name">SCULPTURE-1</p><p class="card-price">$12.00</p></div><span class="buy-button">BUY NOW</span></div></article>
  </div>
  <a class="view-all">VIEW ALL</a>

  <footer class="site-footer">
    <div class="footer-brand"><span class="brand-mark"></span><span class="brand-name">THE MINERAL VAULT</span></div>
    <h3 class="footer-title">Get In Touch With Us</h3>
    <p class="footer-text">At vero eos et accusamus et iusto odio dignissimos ducimus qui<br>blanditiis praesentium voluptatum deleniti atque</p>
    <div class="subscribe"><span class="subscribe-input">Enter Your Email Address</span><span class="subscribe-button">SUBSCRIBE</span></div>
    <ul class="footer-social">
      <li class="social-dot social-dot--1"></li>
      <li class="social-dot social-dot--2"></li>
      <li class="social-dot social-dot--3"></li>
      <li class="social-dot social-dot--4"><svg width="12" height="12" viewBox="0 0 24 24"><path fill="#fff" d="M2 5h20v14H2zm2 2v.5l8 5 8-5V7l-8 5z"/></svg></li>
    </ul>
    <p class="copyright">© Copyrights 2018 The Mineral Vault All Rights Reserved</p>
  </footer>
</section>

<!-- Sold sculptures page -->
<section class="page page--sold">
  <header class="site-header">
    <ul class="contact-list">
      <li><span class="contact-icon"><svg width="10" height="10" viewBox="0 0 24 24"><path fill="#fff" d="M6.6 10.8a15 15 0 0 0 6.6 6.6l2.2-2.2c.3-.3.7-.4 1-.2 1.1.4 2.3.6 3.6.6.6 0 1 .4 1 1V20c0 .6-.4 1-1 1A17 17 0 0 1 3 4c0-.6.4-1 1-1h3.5c.6 0 1 .4 1 1 0 1.3.2 2.5.6 3.6.1.3 0 .7-.2 1z"/></svg></span>(555) 014-2290</li>
      <li><span class="contact-icon"><svg width="10" height="10" viewBox="0 0 24 24"><path fill="#fff" d="M2 5h20v14H2zm2 2v.5l8 5 8-5V7l-8 5z"/></svg></span>mara@pineroverslane.com</li>
    </ul>
    <div class="brand"><span class="brand-mark"></span><span class="brand-name">THE MINERAL VAULT</span></div>
    <ul class="social-list">
      <li class="social-dot social-dot--1"></li>
      <li class="social-dot social-dot--2"></li>
      <li class="social-dot social-dot--3"></li>
      <li class="social-dot social-dot--4"><svg width="12" height="12" viewBox="0 0 24 24"><path fill="#fff" d="M2 5h20v14H2zm2 2v.5l8 5 8-5V7l-8 5z"/></svg></li>
    </ul>
  </header>
  <nav class="main-nav">
    <a href="#">HOME</a><a href="#">ABOUT US</a><a href="#">NEW SCULPTURES</a><a href="#">SOLD SCULPTURES</a><a href="#">CONTACT US</a>
    <svg width="11" height="11" viewBox="0 0 24 24"><circle cx="10" cy="10" r="7" fill="none" stroke="#1d1d1d" stroke-width="3"/><path d="M15 15l7 7" stroke="#1d1d1d" stroke-width="3"/></svg>
  </nav>
  <div class="hero" role="img" aria-label="Close-up photograph of purple amethyst crystals">
    <h1 class="hero-title">SOLD SCULPTURES</h1>
  </div>

  <h2 class="section-title">SOLD SCULPTURES</h2>
  <div class="gallery">
    <article class="card card--sold"><div class="card-photo tone-amber" role="img" aria-label="Amber stone sculpture on a dark stand"><span class="badge">SOLD OUT</span></div><div class="card-body"><p class="card-name">SCULPTURE-1</p><p class="card-price">$12.00</p></div></article>
    <article class="card card--sold"><div class="card-photo tone-linen" role="img" aria-label="Polished geode halves laid beside a cloth pouch"><span class="badge">SOLD OUT</span></div><div class="card-body"><p class="card-name">SCULPTURE-1</p><p class="card-price">$12.00</p></div></article>
    <article class="card card--sold"><div class="card-photo tone-ice" role="img" aria-label="Clear quartz geode held in a hand"><span class="badge">SOLD OUT</span></div><div class="card-body"><p class="card-name">SCULPTURE-1</p><p class="card-price">$12.00</p></div></article>
    <article class="card card--sold"><div class="card-photo tone-geode" role="img" aria-label="Banded agate geode halves on a pink surface"><span class="badge">SOLD OUT</span></div><div class="card-body"><p class="card-name">SCULPTURE-1</p><p class="card-price">$12.00</p></div></article>
    <article class="card card--sold"><div class="card-photo tone-crystal" role="img" aria-label="Iridescent crystal cluster"><span class="badge">SOLD OUT</span></div><div class="card-body"><p class="card-name">SCULPTURE-1</p><p class="card-price">$12.00</p></div></article>
    <article class="card card--sold"><div class="card-photo tone-druzy" role="img" aria-label="Open druzy geode held in hands"><span class="badge">SOLD OUT</span></div><div class="card-body"><p class="card-name">SCULPTURE-1</p><p class="card-price">$12.00</p></div></article>
  </div>
  <a class="view-all">VIEW ALL</a>

  <footer class="site-footer">
    <div class="footer-brand"><span class="brand-mark"></span><span class="brand-name">THE MINERAL VAULT</span></div>
    <h3 class="footer-title">Get In Touch With Us</h3>
    <p class="footer-text">At vero eos et accusamus et iusto odio dignissimos ducimus qui<br>blanditiis praesentium voluptatum deleniti atque</p>
    <div class="subscribe"><span class="subscribe-input">Enter Your Email Address</span><span class="subscribe-button">SUBSCRIBE</span></div>
    <ul class="footer-social">
      <li class="social-dot social-dot--1"></li>
      <li class="social-dot social-dot--2"></li>
      <li class="social-dot social-dot--3"></li>
      <li class="social-dot social-dot--4"><svg width="12" height="12" viewBox="0 0 24 24"><path fill="#fff" d="M2 5h20v14H2zm2 2v.5l8 5 8-5V7l-8 5z"/></svg></li>
    </ul>
    <p class="copyright">© Copyrights 2018 The Mineral Vault All Rights Reserved</p>
  </footer>
</section>

</body>
</html>
```